Birch Hauling Business Card Design Project

We need a new company business card. We provide professional timber harvesting (logging) and forest management services. I'm open to any creative design. Most company caps and shirts are navy blue and Light grey. Logo does not necessarily have to contain those colors. Logo containing picture of logging equipment, log truck, trees, or logs are acceptable. Be creative. Final logo should communicate our company's pride and professionalism in the East Texas Timber Industry.
Updates

Target Market(s)

Timber owners, sawmills, and forestry professionals

Industry/Entity Type

Business

Requirements
Must have
• Must have Contact Info.
Phone: 903-555-0142
address: PO Box 4830
Pine Hollow, Tx 75990
www.jmbirchhauling.example
jmbirchhauling@mailbox.example
Owner: Jared Marsh

Or design must leave room for this info.

```html
<!DOCTYPE html>
<html lang="en">
<head>
<meta charset="utf-8">
<title>J.M. Birch Hauling Company – Business Card</title>
<link rel="stylesheet" href="https://fonts.googleapis.com/css2?family=Questrial&family=Didact+Gothic&display=swap">
<style>
  :root {
    --page: #e4e4e2;
    --green: #93c052;
    --green-deep: #7eab3c;
    --brown: #4a2313;
    --brown-deep: #2f0f06;
    --back-brown: #3a1208;
    --ink: #1b1b1b;
    --white: #ffffff;
  }
  * { margin: 0; padding: 0; box-sizing: border-box; }
  html, body {
    width: 1200px; height: 864px; overflow: hidden;
    background: var(--page);
    font-family: "Questrial", "Didact Gothic", sans-serif;
  }
  .sheet {
    position: relative; width: 1200px; height: 864px;
    display: flex; flex-direction: column; align-items: center; justify-content: center; gap: 40px;
  }
  .card {
    position: relative; width: 640px; height: 366px; overflow: hidden;
    box-shadow: 0 6px 18px rgba(0,0,0,0.18);
  }
  .card-art { position: absolute; inset: 0; width: 100%; height: 100%; }

  /* front */
  .front-title {
    position: absolute; left: 44px; top: 30px;
    color: var(--green); font-size: 27px; font-weight: 400; line-height: 1.12; letter-spacing: 1.5px;
    text-transform: uppercase;
  }
  .contact-list {
    position: absolute; left: 44px; top: 124px; list-style: none;
    color: var(--green); font-size: 13.5px; letter-spacing: 0.6px; line-height: 22px;
  }
  .contact-list li { display: flex; align-items: center; gap: 8px; white-space: nowrap; }
  .contact-icon { width: 12px; height: 12px; flex: none; }
  .owner {
    position: absolute; right: 56px; bottom: 34px; color: var(--ink);
  }
  .owner-role { font-size: 10px; display: block; margin-bottom: -2px; }
  .owner-name { font-size: 20px; font-weight: 700; letter-spacing: 1px; text-transform: uppercase; font-family: "Didact Gothic", "Questrial", sans-serif; }

  /* back */
  .back-title {
    position: absolute; right: 44px; bottom: 58px;
    color: var(--white); font-size: 27px; font-weight: 400; line-height: 1.15; letter-spacing: 1.5px;
    text-transform: uppercase;
  }
  .back-title .initials { display: block; padding-left: 76px; }
</style>
</head>
<body>
<main class="sheet">

  <section class="card card-front" aria-label="Business card front">
    <svg class="card-art" viewBox="0 0 640 366" preserveAspectRatio="none" aria-hidden="true">
      <defs>
        <linearGradient id="frontGreen" x1="0" y1="0" x2="1" y2="1">
          <stop offset="0" stop-color="var(--green)"/>
          <stop offset="1" stop-color="var(--green-deep)"/>
        </linearGradient>
        <radialGradient id="frontBrown" cx="0.6" cy="0.55" r="0.8">
          <stop offset="0" stop-color="var(--brown)"/>
          <stop offset="1" stop-color="var(--brown-deep)"/>
        </radialGradient>
      </defs>
      <rect width="640" height="366" fill="url(#frontGreen)"/>
      <path d="M0,0 L390,0 C480,30 540,130 525,200 C510,265 460,292 380,292 C250,292 110,262 0,222 Z" fill="url(#frontBrown)"/>
      <path d="M390,0 C480,30 540,130 525,200 C510,265 460,292 380,292 C250,292 110,262 0,222" fill="none" stroke="var(--white)" stroke-width="3"/>
    </svg>

    <h1 class="front-title">J.M. Birch<br>Hauling Company</h1>

    <ul class="contact-list">
      <li>
        <svg class="contact-icon" viewBox="0 0 12 12" aria-hidden="true"><circle cx="6" cy="3.6" r="2.6" fill="var(--white)"/><path d="M1 12 C1 7.5 11 7.5 11 12 Z" fill="var(--white)"/></svg>
        <span>903-555-0142</span>
      </li>
      <li>
        <svg class="contact-icon" viewBox="0 0 12 12" aria-hidden="true"><circle cx="6" cy="6" r="5" fill="none" stroke="var(--white)" stroke-width="1.2"/><ellipse cx="6" cy="6" rx="2" ry="5" fill="none" stroke="var(--white)" stroke-width="1"/><line x1="1" y1="6" x2="11" y2="6" stroke="var(--white)" stroke-width="1"/></svg>
        <span>www.jmbirchhauling.example</span>
      </li>
      <li>
        <svg class="contact-icon" viewBox="0 0 12 12" aria-hidden="true"><rect x="0.6" y="2.4" width="10.8" height="7.4" fill="none" stroke="var(--white)" stroke-width="1.2"/><path d="M0.6 2.6 L6 6.8 L11.4 2.6" fill="none" stroke="var(--white)" stroke-width="1.2"/></svg>
        <span>jmbirchhauling@mailbox.example</span>
      </li>
      <li><span>PO Box 4830 Pine Hollow, Tx 75990</span></li>
    </ul>

    <p class="owner"><span class="owner-role">Owner</span><span class="owner-name">Jared Marsh</span></p>
  </section>

  <section class="card card-back" aria-label="Business card back">
    <svg class="card-art" viewBox="0 0 640 366" preserveAspectRatio="none" aria-hidden="true">
      <defs>
        <linearGradient id="backGreen" x1="0" y1="0" x2="1" y2="1">
          <stop offset="0" stop-color="var(--green-deep)"/>
          <stop offset="0.5" stop-color="var(--green)"/>
          <stop offset="1" stop-color="var(--green-deep)"/>
        </linearGradient>
      </defs>
      <rect width="640" height="366" fill="var(--back-brown)"/>
      <path d="M0,0 H640 V122 C575,190 440,200 330,190 C200,178 80,140 0,104 Z" fill="url(#backGreen)"/>
      <path d="M640,122 C575,190 440,200 330,190 C200,178 80,140 0,104" fill="none" stroke="var(--white)" stroke-width="3"/>
    </svg>
    <h2 class="back-title"><span class="initials">J.M. Birch</span>Hauling Company</h2>
  </section>

</main>
</body>
</html>
```